A new presentation to our clients

we are a Real Estate agency, our website is www.lumibrasa.com and it’s time to have a new, fashion and remarcable Business Card. we want to differentiate ourselves from other companies so we want a business card that differentiates us. we want the business card to impact our customers. in the competitive market that we have today, we have to be different and it is this difference that we seek

Target Market(s)

Real Estate Clients

Contact Information for Business Card

We search a totaly diferent card from the usual

Font styles to use
Sans Serif

Colors
e34197

Requirements
Must have
• Logo, adress, phone contact, e-mail, photo, and our website
Nice to have
• We would like to see a modern business card
Should not have
• Houses or building draws

```html
<!DOCTYPE html>
<html lang="en">
<head>
<meta charset="utf-8">
<title>Lumibrasa Business Card</title>
<link href="https://fonts.googleapis.com/css2?family=Arimo:wght@400&display=swap" rel="stylesheet">
<style>
  :root {
    --brand-pink: #e8267a;
    --wave-edge: #4a4a4a;
    --card-white: #ffffff;
    --stage-dark: #1c1c1c;
    --stage-light: #5e5e5e;
    --ink-light: #ffffff;
  }
  * { margin: 0; padding: 0; box-sizing: border-box; }
  html, body {
    width: 1200px;
    height: 960px;
    overflow: hidden;
  }
  body {
    background: radial-gradient(ellipse at 50% 50%, var(--stage-light) 0%, var(--stage-dark) 75%);
    font-family: "Arimo", Arial, sans-serif;
    position: relative;
  }
  .business-card {
    position: absolute;
    left: 150px;
    top: 220px;
    width: 900px;
    height: 520px;
    border-radius: 34px;
    overflow: hidden;
    background: var(--card-white);
    box-shadow: 0 14px 40px rgba(0,0,0,0.45);
  }
  .wave-band {
    position: absolute;
    inset: 0;
    width: 100%;
    height: 100%;
  }
  .wordmark {
    position: absolute;
    left: 78px;
    top: 150px;
    font-size: 70px;
    line-height: 1;
    font-weight: 400;
    color: var(--brand-pink);
    letter-spacing: 2px;
    white-space: nowrap;
    z-index: 1;
  }
  .contact-block {
    position: absolute;
    right: 44px;
    top: 250px;
    text-align: right;
    color: var(--ink-light);
    z-index: 1;
  }
  .person-name {
    font-size: 30px;
    line-height: 1.05;
  }
  .person-role {
    font-size: 22px;
    margin-bottom: 26px;
    padding-right: 34px;
  }
  .contact-line {
    display: flex;
    justify-content: flex-end;
    align-items: center;
    gap: 10px;
    font-size: 19px;
    line-height: 1.45;
  }
  .contact-icon {
    width: 18px;
    height: 18px;
    flex: none;
  }
  .office-address {
    position: absolute;
    left: 48px;
    bottom: 40px;
    color: var(--ink-light);
    font-size: 21px;
    line-height: 1.3;
    z-index: 1;
  }
</style>
</head>
<body>
  <div class="business-card">
    <svg class="wave-band" viewBox="0 0 900 520" preserveAspectRatio="none" aria-hidden="true">
      <path d="M0,396 C290,428 410,326 530,226 S730,100 900,88 L900,520 L0,520 Z" fill="var(--wave-edge)"/>
      <path d="M0,408 C290,440 415,338 536,238 S735,114 900,102 L900,520 L0,520 Z" fill="var(--brand-pink)"/>
    </svg>

    <div class="wordmark">Lumibrasa</div>

    <div class="contact-block">
      <div class="person-name">MARCO ALVES</div>
      <div class="person-role">CEO/FOUNDER</div>

      <div class="contact-line">(+351) 220 481 506
        <svg class="contact-icon" viewBox="0 0 24 24"><path fill="#fff" d="M6.6 10.8a15 15 0 0 0 6.6 6.6l2.2-2.2a1 1 0 0 1 1-.25 11.4 11.4 0 0 0 3.6.6 1 1 0 0 1 1 1V20a1 1 0 0 1-1 1A17 17 0 0 1 3 4a1 1 0 0 1 1-1h3.5a1 1 0 0 1 1 1c0 1.25.2 2.45.6 3.6a1 1 0 0 1-.25 1z"/></svg>
      </div>
      <div class="contact-line">(+351) 220 481 509
        <svg class="contact-icon" viewBox="0 0 24 24"><rect x="6" y="3" width="12" height="6" fill="#fff"/><rect x="2" y="10" width="20" height="8" rx="2" fill="#fff"/><rect x="6" y="15" width="12" height="6" fill="#fff" stroke="var(--brand-pink)" stroke-width="1.5"/></svg>
      </div>
      <div class="contact-line">geral@lumibrasa.com
        <svg class="contact-icon" viewBox="0 0 24 24"><rect x="2" y="5" width="20" height="14" rx="1.5" fill="#fff"/><path d="M2.5 6 12 13l9.5-7" fill="none" stroke="var(--brand-pink)" stroke-width="1.6"/></svg>
      </div>
      <div class="contact-line">www.lumibrasa.com
        <svg class="contact-icon" viewBox="0 0 24 24"><circle cx="12" cy="12" r="10" fill="#fff"/><ellipse cx="12" cy="12" rx="4" ry="10" fill="none" stroke="var(--brand-pink)" stroke-width="1.5"/><path d="M2 12h20" stroke="var(--brand-pink)" stroke-width="1.5"/></svg>
      </div>
    </div>

    <div class="office-address">
      Rua do Sol Nascente, 87<br>
      4400-210, Vila Nova de Gaia
    </div>
  </div>
</body>
</html>
```